Quill Press Oceania needs a website

We require a website design which will be different to the normal websites that you visit. The objective of this website will be a call to action on the last page which will link to our email address so customers can email us their quotation requirements.

An example of how we envisage the look and the pages turning is as a flip books for example: https://www.vidharbor.example/watch?v=KtLmPzQa7Rw&feature=vh.be

page 1: just has our logo on it with the tag "Specialist producing quality printed books to your deadline."

Page 2: Black Page with white text "Black and White Book"
These are produced either digitally or offset on a complete range of stocks

Page 3: Colour books (use an image of your choice) These are also produced either digitally or offset plus we have the choice of web presses for larger print runs

Page 4: Digital books We do have a minimum run of 50 books using this process so a one off Thesis is not economically viable using this process. In special circumstance the digital process can produce books more quickly then by using our offset printing process.

Page 5: Having the complete range of printing machines at our disposal enables you to make a perfectly informed choice for your special project.

Then we need a special quote button which takes them directly to our email link. On this page we also need to add: We have had 25 years' experience printing books saving customers time and money whilst guaranteeing quality

Page 6: Logo repeated from page one with name: Morgan Elsworth and mobile phone no 0487 552 314

- Must follow the brief exactly. Must have a turn page book. Clear, simple and concise with a touch of creative flare and must lead into a call for action which is there quotation. A unique button for quotation link...something out of the ordinary which makes someone want to get a quote.

- It would be nice to have 3D Logo on Page 1 & 6.
a unique button for quotation link...something that make someone eager to proceed.

Our main objective is that they should not leave our website without giving us a quote. Please make sure that the spelling is correct and we do not require clip art images. Continue the logo colours through the theme
Updates

here is another example www.vidharbor.example/watch?v=JbXo412TrGe Added Saturday, May 13, 2017

Target Market(s)

Schools, Universities, Self Publishers, Publishers, Graphic Designers, Conference Providers, Businesses, Corporations, Government.

Industry/Entity Type

Printing

Coding

Coded - Design and coding required

Number of Pages Required

5+ page

Font styles to use
Sans Serif

Colors
34a6d7
ec1f27
fbed22
9bcb3c
ffc214
6b449b

Requirements
Must have
• Must follow the brief exactly. Must have a turn page book. Clear, simple and concise with a touch of creative flare and must lead into a call for action which is there quotation. A unique button for quotation link...something out of the ordinary which makes someone want to get a quote. would like to see the colours of the logo use throughout
Nice to have
• 3D Logo on Page 1 & 6.
• a unique button for quotation link...something that make someone eager to proceed.
• Our main objective is that they should not leave our website without giving us a quote
Should not have
• Spelling mistakes, clip art, ordinary design

```html
<!DOCTYPE html>
<html lang="en">
<head>
<meta charset="utf-8">
<title>Colors Book – Quill Press Oceania</title>
<link rel="stylesheet" href="https://fonts.googleapis.com/css2?family=Montserrat:wght@600&family=Questrial&display=swap">
<style>
  :root {
    --page-white: #ffffff;
    --haze-top: #f1f1f2;
    --haze-bottom: #fafafa;
    --brand-red: #ec1f27;
    --brand-blue: #34a6d7;
    --brand-yellow: #ffc214;
    --brand-green: #9bcb3c;
    --brand-purple: #6b449b;
    --tone-orange: #f37021;
    --tone-magenta: #d4237a;
    --tone-teal: #1cc3a8;
    --body-grey: #8c8c8c;
  }
  * { margin: 0; padding: 0; box-sizing: border-box; }
  html, body {
    width: 720px;
    height: 1200px;
    overflow: hidden;
    background: var(--page-white);
  }
  .book-page {
    position: relative;
    width: 720px;
    height: 1200px;
    overflow: hidden;
    background: var(--page-white);
  }
  .hero-band {
    position: absolute;
    left: 0; top: 0;
    width: 720px; height: 612px;
    background: linear-gradient(180deg, var(--haze-top) 0%, var(--haze-bottom) 100%);
  }
  .hero-artwork {
    position: absolute;
    left: 14px; top: 78px;
    width: 700px; height: 440px;
    border-radius: 24px;
    background: linear-gradient(90deg,
      var(--brand-yellow) 0%,
      var(--tone-orange) 25%,
      var(--tone-magenta) 45%,
      var(--brand-purple) 55%,
      var(--brand-blue) 75%,
      var(--tone-teal) 100%);
    opacity: 0.55;
  }
  .page-title {
    position: absolute;
    left: 0; right: 0; top: 639px;
    text-align: center;
    font-family: "Montserrat", sans-serif;
    font-weight: 600;
    font-size: 50px;
    letter-spacing: -0.5px;
    line-height: 1;
  }
  .page-title .title-colors { color: var(--brand-red); }
  .page-title .title-book { color: var(--brand-blue); }
  .page-copy {
    position: absolute;
    left: 0; right: 0; top: 717px;
    text-align: center;
    font-family: "Questrial", sans-serif;
    font-size: 29px;
    line-height: 41.6px;
    color: var(--body-grey);
    letter-spacing: 0.6px;
  }
  .page-copy .copy-line {
    display: block;
    white-space: nowrap;
  }
  .footer-artwork {
    position: absolute;
    left: 0; top: 1040px;
    width: 720px; height: 160px;
    background: linear-gradient(90deg,
      var(--tone-magenta) 0%,
      var(--tone-orange) 35%,
      var(--brand-yellow) 60%,
      var(--brand-green) 78%,
      var(--brand-blue) 100%);
    opacity: 0.45;
  }
</style>
</head>
<body>
<main class="book-page">
  <div class="hero-band"></div>
  <div class="hero-artwork" role="img" aria-label="Colourful ink splash illustration in yellow, orange, magenta, purple, blue and teal around a stack of books"></div>

  <h1 class="page-title"><span class="title-colors">Colors</span> <span class="title-book">Book</span></h1>

  <p class="page-copy">
    <span class="copy-line">These are also produced either digitally</span>
    <span class="copy-line">or offset plus we have the choice of web</span>
    <span class="copy-line">presses for larger print runs</span>
  </p>

  <div class="footer-artwork" role="img" aria-label="Flowing rainbow ribbon artwork from pink to blue"></div>
</main>
</body>
</html>
```